new construction company branding

branding

Can I have a banner made so I can hang it as 1) branding my jobsite 2) advertisement

Target Market(s)

Commercial

Industry/Entity Type

Construction Trade

Font styles to use
Other font styles liked:
• Cinzel bold

Colors
EB3D1F
EC4F4E
F09395
F8D3D4
FCEDEE

Requirements
Must have
• Bright colors for advertisement
Nice to have
• 36”x48” canvas
Should not have
• To busy

```html
<!DOCTYPE html>
<html lang="en">
<head>
<meta charset="utf-8">
<title>Northbeam Build Jobsite Banner</title>
<link href="https://fonts.googleapis.com/css2?family=Cinzel:wght@700&family=Montserrat:wght@600;700;800&display=swap" rel="stylesheet">
<style>
  :root {
    --stage: #d1d1d1;
    --brand-red: #e10e10;
    --ink: #1f1f1f;
    --white: #ffffff;
    --sky-top: #3a8fcf;
    --sky-light: #5aa3d8;
    --timber: #c9a577;
    --timber-dark: #a9845a;
  }
  * { margin: 0; padding: 0; box-sizing: border-box; }
  html, body {
    width: 1200px; height: 720px; overflow: hidden;
    background: var(--stage);
  }
  .banner {
    position: absolute; left: 40px; top: 195px;
    width: 1129px; height: 339px; overflow: hidden;
  }
  .site-photo {
    position: absolute; inset: 0;
    background:
      linear-gradient(100deg, var(--timber-dark) 0%, var(--timber) 28%, rgba(201,165,119,0.6) 40%, rgba(90,163,216,0) 52%),
      linear-gradient(180deg, var(--sky-top) 0%, var(--sky-light) 60%, var(--sky-top) 100%);
  }
  .shapes { position: absolute; inset: 0; }
  .brand {
    position: absolute; left: 0; top: 62px; width: 1260px;
    text-align: center;
  }
  .brand-name {
    font-family: "Cinzel", serif; font-weight: 700;
    font-size: 20px; color: var(--white); letter-spacing: 0.5px;
  }
  .brand-trade {
    margin-top: 4px;
    font-family: "Cinzel", serif; font-weight: 700;
    font-size: 13px; color: var(--brand-red); letter-spacing: 4.5px;
  }
  .headline {
    position: absolute;
    font-family: "Montserrat", sans-serif; font-weight: 800;
    color: var(--white); font-size: 46px; line-height: 1; letter-spacing: 1px;
    white-space: nowrap;
  }
  .headline--top { left: 552px; top: 142px; }
  .headline--bottom { left: 469px; top: 198px; }
  .phone {
    position: absolute; left: 14px; top: 290px;
    display: flex; align-items: center; gap: 8px;
    font-family: "Montserrat", sans-serif; font-weight: 800;
    font-size: 48px; line-height: 1; color: var(--white); letter-spacing: -0.5px;
  }
  .website {
    position: absolute; left: 440px; top: 306px;
    display: flex; align-items: center; gap: 7px;
    font-family: "Montserrat", sans-serif; font-weight: 600;
    font-size: 20px; color: var(--white);
  }
</style>
</head>
<body>
  <section class="banner">
    <div class="site-photo" role="img" aria-label="Photo of timber house framing against a blue sky"></div>

    <svg class="shapes" width="1129" height="339" viewBox="0 0 1129 339" aria-hidden="true">
      <polygon points="402,172 513,172 559,129 1005,129 876,258 482,258" fill="var(--brand-red)"/>
      <polygon points="880,339 1129,78 1129,339" fill="var(--white)"/>
      <path d="M955,339 C1000,230 1060,160 1129,90 L1129,339 Z" fill="var(--ink)"/>
      <polygon points="735,339 1070,0 1129,0 1129,8 806,339" fill="var(--brand-red)"/>
      <polygon points="0,285 476,285 422,339 0,339" fill="var(--brand-red)"/>
      <polygon points="448,300 748,300 712,339 420,339" fill="var(--ink)"/>
    </svg>

    <div class="brand">
      <div class="brand-name">NORTHBEAM BUILD INC LLC</div>
      <div class="brand-trade">GENERAL CONTRACTOR</div>
    </div>

    <div class="headline headline--top">HELPING YOU</div>
    <div class="headline headline--bottom">BUILD BETTER</div>

    <div class="phone">
      <svg width="22" height="40" viewBox="0 0 22 40" aria-hidden="true">
        <rect x="1.5" y="1.5" width="19" height="37" rx="3" fill="var(--brand-red)" stroke="var(--white)" stroke-width="3"/>
        <rect x="8" y="33" width="6" height="2" fill="var(--white)"/>
      </svg>
      <span>555-0142-789</span>
    </div>

    <div class="website">
      <svg width="14" height="14" viewBox="0 0 14 14" aria-hidden="true">
        <circle cx="7" cy="7" r="6" fill="none" stroke="var(--white)" stroke-width="1.4"/>
        <ellipse cx="7" cy="7" rx="2.6" ry="6" fill="none" stroke="var(--white)" stroke-width="1.2"/>
        <line x1="1" y1="7" x2="13" y2="7" stroke="var(--white)" stroke-width="1.2"/>
      </svg>
      <span>www.northbeambuild.com</span>
    </div>
  </section>
</body>
</html>
```